Modern business card design for professional copywriter

I'd like a business card design that I can use to have my cards printed out by quillprint.com as a squared corners business card (see artwork and design guidelines here: https://help.quillprint.com/hc/en-gb/sections/200570950-QUILL-Product-Templates)

The design should be clean and modern and reflect the colours, tone and branding on my website: https://tessavorrin.com.au

Target Market(s)

Professionals, B2B small business owners

Industry/Entity Type

Business

Contact Information for Business Card

Tessa Vorrin
m: 0468 905 327
e: tessa@tessavorrin.com.au
w: tessavorrin.com.au

Font styles to use
Sans Serif

Requirements
Must have
• Tagline: "Sharp, honest words for busy, ambitious teams"
• Brand colours: fd8000, 009984, 666666 and black
Nice to have

```html
<!DOCTYPE html>
<html lang="en">
<head>
<meta charset="utf-8">
<title>Tessa Vorrin – Business Card</title>
<link href="https://fonts.googleapis.com/css2?family=Jost:wght@400;500&family=Oswald:wght@500&display=swap" rel="stylesheet">
<style>
  :root {
    --backdrop: #262626;
    --card: #121212;
    --ink-gloss: #6f6f6f;
    --ink-soft: #5c5c5c;
    --ink-line: #4a4a4a;
  }
  * { box-sizing: border-box; margin: 0; padding: 0; }
  html, body {
    width: 1200px; height: 900px; overflow: hidden;
    background: var(--backdrop);
  }
  .stage {
    width: 1200px; height: 900px;
    display: flex; flex-direction: column; align-items: center; justify-content: center;
    gap: 50px;
  }
  .card {
    width: 580px; height: 375px;
    background: var(--card);
    position: relative;
    box-shadow: 0 12px 30px rgba(0,0,0,.45);
  }
  .brand {
    display: flex; align-items: center; gap: 12px;
    font-family: "Jost", sans-serif; font-weight: 500;
    color: var(--ink-gloss);
    letter-spacing: .5px;
    white-space: nowrap;
  }
  .brand-mark { width: 16px; height: 16px; background: var(--ink-gloss); }
  .card-front { display: flex; align-items: center; justify-content: center; }
  .card-front .brand { font-size: 46px; }
  .card-back .brand {
    position: absolute; top: 58px; left: 0; right: 0; justify-content: center;
    font-size: 40px;
  }
  .card-back .brand-mark { width: 14px; height: 14px; }
  .details {
    position: absolute; top: 172px; left: 30px; right: 30px;
    display: flex; align-items: center; justify-content: center;
  }
  .identity { text-align: right; padding-right: 20px; white-space: nowrap; }
  .identity-name {
    font-family: "Oswald", sans-serif; font-weight: 500;
    font-size: 30px; letter-spacing: 1px; color: var(--ink-gloss); line-height: 1.1;
  }
  .identity-role {
    font-family: "Jost", sans-serif; font-size: 19px; color: var(--ink-soft);
    letter-spacing: 1px; margin-top: 2px;
  }
  .divider { width: 1px; height: 76px; background: var(--ink-line); flex: none; }
  .contacts { list-style: none; padding-left: 20px; }
  .contacts li {
    display: flex; align-items: center; gap: 12px;
    font-family: "Jost", sans-serif; font-size: 16px; letter-spacing: 1px;
    color: var(--ink-gloss); line-height: 25px; white-space: nowrap;
  }
  .contacts svg { width: 13px; height: 13px; flex: none; }
  .tagline {
    position: absolute; bottom: 48px; left: 0; right: 0; text-align: center;
    font-family: "Jost", sans-serif; font-size: 17px; letter-spacing: 1.5px;
    color: var(--ink-soft); white-space: nowrap;
  }
</style>
</head>
<body>
<main class="stage">
  <section class="card card-front" aria-label="Card front">
    <div class="brand"><span class="brand-mark"></span>Tessa Vorrin</div>
  </section>

  <section class="card card-back" aria-label="Card back">
    <div class="brand"><span class="brand-mark"></span>Tessa Vorrin</div>
    <div class="details">
      <div class="identity">
        <p class="identity-name">TESSA VORRIN</p>
        <p class="identity-role">Copywriter</p>
      </div>
      <div class="divider"></div>
      <ul class="contacts">
        <li>
          <svg viewBox="0 0 14 14" aria-hidden="true"><rect x="3.5" y="1" width="7" height="12" rx="1.2" fill="none" stroke="#6f6f6f" stroke-width="1.3"/></svg>
          0468 905 327
        </li>
        <li>
          <svg viewBox="0 0 14 14" aria-hidden="true"><rect x="1" y="3" width="12" height="8.5" fill="#6f6f6f"/><path d="M1 3 L7 8 L13 3" fill="none" stroke="#121212" stroke-width="1.2"/></svg>
          tessa@tessavorrin.com.au
        </li>
        <li>
          <svg viewBox="0 0 14 14" aria-hidden="true"><circle cx="6" cy="6" r="4" fill="none" stroke="#6f6f6f" stroke-width="1.6"/><path d="M9 9 L13 13" stroke="#6f6f6f" stroke-width="1.8"/></svg>
          tessavorrin.com.au
        </li>
      </ul>
    </div>
    <p class="tagline">Sharp, honest words for busy, ambitious teams</p>
  </section>
</main>
</body>
</html>
```